Business card design

I am open to ideas. I was thinking of a vertical design, turning the name 90 degrees and placing it on the left edge, then some clipped portion of the fabulous tree with contact info on the bottom -- special emphasis on Web address:WhimBeads.comFor All Your Beading Needs121 E. Cotati AveCotati, CA 94931(707) 664-8343

```html
<!DOCTYPE html>
<html lang="en">
<head>
<meta charset="utf-8">
<title>Fern Glass Co. – Business Card</title>
<link rel="stylesheet" href="https://fonts.googleapis.com/css2?family=Roboto:wght@400;500&display=swap">
<style>
  :root {
    --backdrop: #8a8a8a;
    --card: #ffffff;
    --ink: #1a1a1a;
    --rule: #6f6f6f;
    --accent-green: #2f8a12;
  }
  html, body {
    margin: 0;
    padding: 0;
    width: 1200px;
    height: 900px;
    overflow: hidden;
    background: var(--backdrop);
    font-family: "Roboto", Arial, sans-serif;
  }
  .canvas {
    position: relative;
    width: 1200px;
    height: 900px;
  }
  .business-card {
    position: absolute;
    left: 433px;
    top: 200px;
    width: 310px;
    height: 502px;
    background: var(--card);
    border-radius: 62px 0 62px 0;
    color: var(--ink);
    text-align: center;
  }
  .brand-name {
    position: absolute;
    left: 0;
    right: 0;
    top: 178px;
    margin: 0;
    font-size: 27px;
    font-weight: 400;
    letter-spacing: 0.5px;
    color: var(--ink);
  }
  .address {
    position: absolute;
    left: 0;
    right: 0;
    top: 238px;
    margin: 0;
    font-size: 14px;
    line-height: 18px;
    font-style: normal;
  }
  .divider {
    position: absolute;
    left: 60px;
    width: 190px;
    height: 10px;
  }
  .divider--upper { top: 293px; }
  .divider--lower { top: 383px; }
  .contact {
    position: absolute;
    left: 0;
    right: 0;
    top: 322px;
    margin: 0;
  }
  .contact__phone {
    display: block;
    font-size: 17px;
    line-height: 21px;
  }
  .contact__web {
    display: block;
    font-size: 16px;
    font-weight: 500;
    line-height: 21px;
  }
  .tagline {
    position: absolute;
    left: 0;
    right: 0;
    top: 406px;
    margin: 0;
    font-size: 16px;
    color: var(--accent-green);
  }
</style>
</head>
<body>
<main class="canvas">
  <section class="business-card">
    <h1 class="brand-name">Fern Glass Co.</h1>
    <address class="address">348 W. Brindle Ave<br>Alder Falls, CA 94960</address>
    <svg class="divider divider--upper" viewBox="0 0 190 10" aria-hidden="true">
      <line x1="0" y1="5" x2="80" y2="5" stroke="var(--rule)" stroke-width="1"/>
      <circle cx="95" cy="5" r="3" fill="var(--rule)"/>
      <line x1="110" y1="5" x2="190" y2="5" stroke="var(--rule)" stroke-width="1"/>
    </svg>
    <p class="contact">
      <span class="contact__phone">(707) 555-0192</span>
      <span class="contact__web">www.FernGlassco.com</span>
    </p>
    <svg class="divider divider--lower" viewBox="0 0 190 10" aria-hidden="true">
      <line x1="0" y1="5" x2="80" y2="5" stroke="var(--rule)" stroke-width="1"/>
      <circle cx="95" cy="5" r="3" fill="var(--rule)"/>
      <line x1="110" y1="5" x2="190" y2="5" stroke="var(--rule)" stroke-width="1"/>
    </svg>
    <p class="tagline">For All Your Beading Needs</p>
  </section>
</main>
</body>
</html>
```